Mental Health care Company in Washington DC

We are a new mental health care services provider in Washington DC. Please look at these sites.
https://brightwaterfamilysupport.com
https://www.quietharborinc.com
https://willowgate-dc.org/
https://www.tidepathdc.com
https://www.thelanternofdc.com

```html
<!DOCTYPE html>
<html lang="en">
<head>
<meta charset="utf-8">
<title>Calder Health Services — Mental Wellness in Washington DC</title>
<link href="https://fonts.googleapis.com/css2?family=Inter:wght@400;500;600;700&family=Poppins:wght@400;500;600;700&display=swap" rel="stylesheet">
<style>
:root{
  --orange:#F5822A;
  --navy:#0D1F3F;
  --navy-deep:#0A1832;
  --peach:#FCE8D8;
  --ink:#1B2230;
  --muted:#4A5160;
  --line:#D5D8DE;
  --white:#FFFFFF;
  --field:#EDEDED;
}
*{box-sizing:border-box;margin:0;padding:0}
html,body{width:1200px;height:3827px;overflow:hidden}
body{position:relative;background:var(--white);font-family:"Inter",sans-serif;color:var(--ink)}
.abs{position:absolute}
a{color:inherit;text-decoration:none}

/* Header */
.topbar{left:472px;top:0;width:728px;height:30px;background:var(--navy);clip-path:polygon(0 0,100% 0,100% 100%,18px 100%);display:flex;align-items:center;justify-content:flex-end;gap:30px;padding-right:100px;font-size:11px;color:#fff}
.topbar span{display:flex;align-items:center;gap:6px}
.topbar-accent{left:468px;top:0;width:28px;height:30px;background:var(--orange);clip-path:polygon(0 0,40% 0,100% 100%,60% 100%)}
.brand{left:92px;top:24px;font-family:"Poppins",sans-serif;color:var(--navy)}
.brand .name{font-size:31px;font-weight:500;line-height:1;display:flex;align-items:center;gap:8px}
.brand .dot{width:9px;height:9px;border-radius:50%;background:var(--orange)}
.brand .tag{font-size:10px;letter-spacing:7px;color:var(--muted);margin-top:4px;padding-left:30px}
.nav{left:553px;top:54px;display:flex;gap:40px;font-size:13px;color:var(--ink)}
.nav .active{color:var(--orange)}
.btn-contact{left:995px;top:47px;width:106px;height:29px;border-radius:15px;background:var(--orange);color:#fff;font-size:11px;font-weight:600;display:flex;align-items:center;justify-content:center}

/* Hero */
.hero-photo{left:0;top:92px;width:1200px;height:529px;background:linear-gradient(100deg,#7a6a5e 0%,#b9b3aa 30%,#d9dcde 55%,#c7ccd0 75%,#9aa2a6 100%)}
.hero-card{left:131px;top:208px;width:496px;height:297px;background:#fff;border-radius:12px;text-align:center;padding-top:36px}
.hero-card h1{font-family:"Poppins",sans-serif;font-weight:400;font-size:30px;line-height:44px;color:var(--navy);letter-spacing:.5px}
.hero-card h1 b{color:var(--orange);font-weight:600}
.hero-card p{font-size:14px;line-height:22px;color:var(--muted);margin:16px auto 0;width:400px}
.subscribe{display:flex;border-radius:12px;overflow:hidden;height:60px}
.subscribe .field{flex:1;background:var(--field);font-size:12px;font-weight:500;display:flex;align-items:center;padding-left:22px;color:var(--ink)}
.subscribe .go{width:102px;background:var(--navy);color:#fff;font-size:12px;font-weight:600;display:flex;align-items:center;justify-content:center}
.hero-card .subscribe{position:absolute;left:33px;top:203px;width:428px}

/* Section titles */
.sec-title{left:0;width:1200px;text-align:center}
.sec-title h2{font-size:18px;font-weight:600;color:var(--ink)}
.sec-title p{font-size:13px;color:var(--ink);margin-top:5px}
.rule{height:1px;width:110px;background:var(--line)}

/* Service cards */
.svc{width:290px;height:266px;background:#fff;border-radius:8px;box-shadow:0 4px 22px rgba(0,0,0,.08);text-align:center;padding-top:42px}
.svc .icon{height:56px;display:flex;justify-content:center}
.svc .bar{width:64px;height:1px;background:#F5B98A;margin:20px auto 22px}
.svc h3{font-size:16px;font-weight:600;color:var(--ink)}
.svc p{font-size:11.5px;line-height:17px;color:var(--muted);width:220px;margin:10px auto 14px}
.more{font-size:13px;font-weight:500;color:var(--orange);text-decoration:underline;display:inline-flex;align-items:center;gap:8px}
.svc.featured{background:var(--orange)}
.svc.featured h3,.svc.featured p,.svc.featured .more{color:#fff}
.svc.featured .bar{background:rgba(255,255,255,.55)}

/* About */
.about-panel{left:432px;top:1188px;width:679px;height:407px;background:var(--navy)}
.about-figure{left:930px;top:1420px;width:130px;height:175px;background:linear-gradient(180deg,rgba(255,255,255,.05),rgba(255,255,255,.14));border-radius:60px 60px 0 0}
.about-photo{left:88px;top:1233px;width:427px;height:319px;background:linear-gradient(120deg,#a9b3bd,#dfe3e6 45%,#6f7f95);outline:3px solid #fff;outline-offset:0}
.about-text{left:556px;top:1232px;width:470px;color:#fff;font-size:11.5px;line-height:18.5px}
.about-text p{margin-bottom:12px}
.about-text ul{list-style:none;margin-top:-2px}
.about-text li{position:relative;padding-left:14px;margin-bottom:5px}
.about-text li:before{content:"";position:absolute;left:0;top:7px;width:5px;height:5px;border-radius:50%;background:var(--orange)}
.btn-light{background:#fff;color:var(--ink);font-size:13px;font-weight:500;display:inline-flex;align-items:center;gap:6px;padding:0 12px;height:32px}

/* Blog */
.post{width:441px;height:367px;background:#fff;border:1px solid #DADDE2;border-radius:8px;overflow:hidden;box-shadow:0 3px 12px rgba(0,0,0,.05)}
.post .img{height:208px}
.post .body{padding:20px 16px 0}
.post h3{font-size:16px;font-weight:600;color:var(--ink)}
.post p{font-size:11.5px;line-height:17px;color:var(--muted);margin:12px 0 20px}
.btn-dark{left:526px;top:2147px;width:148px;height:42px;background:var(--navy);color:#fff;font-size:13px;font-weight:500;display:flex;align-items:center;justify-content:center;gap:6px;border-radius:3px}

/* Why choose */
.why-panel{left:88px;top:2333px;width:680px;height:404px;background:var(--peach)}
.why-text{left:123px;top:2380px;width:475px;font-size:11.5px;line-height:18.5px;color:var(--muted)}
.why-text p{margin-bottom:12px}
.why-photo{left:686px;top:2376px;width:425px;height:316px;background:radial-gradient(circle at 45% 45%,#f0c48a 0%,#5f8fb5 28%,#1d3e62 65%,#0f2440 100%);outline:3px solid #fff}

/* Testimonials */
.quote{width:241px;height:231px;background:#fff;box-shadow:0 4px 20px rgba(0,0,0,.08);padding:18px 17px}
.stars{display:flex;gap:4px}
.quote p{font-size:10px;line-height:18px;color:var(--ink);margin-top:12px}
.person{display:flex;align-items:center;gap:12px;margin-top:12px}
.avatar{width:48px;height:48px;border-radius:50%;background:linear-gradient(160deg,#d9c7b8,#8a6d5c)}
.person b{display:block;font-family:"Poppins",sans-serif;font-size:16px;font-weight:600;color:var(--navy)}
.person span{font-family:"Poppins",sans-serif;font-size:11px;color:var(--navy)}
.dots{left:586px;top:3133px;display:flex;gap:3px}
.dots i{width:3px;height:3px;border-radius:50%;background:var(--orange)}

/* Newsletter */
.news-band{left:0;top:3274px;width:1200px;height:283px;background:linear-gradient(90deg,#E9782A,#F5822A 40%,#F08A3A)}
.news-photo{left:757px;top:3185px;width:283px;height:372px;background:linear-gradient(180deg,rgba(255,255,255,0) 0%,#eef0f2 40%,#d8dde2 100%);border-radius:140px 140px 0 0}
.news-title{left:141px;top:3323px;font-size:29px;font-weight:700;color:#fff}
.news-copy{left:141px;top:3371px;width:500px;font-size:13.5px;line-height:21px;color:#fff}
.news-form{left:141px;top:3442px;width:402px;height:58px}
.news-form .field{background:#fff}

/* Footer */
.footer{left:0;top:3557px;width:1200px;height:239px;background:var(--navy)}
.footer-bottom{left:0;top:3796px;width:1200px;height:31px;background:var(--navy-deep);color:#fff;font-size:8.5px;display:flex;align-items:center;justify-content:center}
.fbrand{left:144px;top:3618px;color:#fff;font-family:"Poppins",sans-serif}
.fbrand .name{font-size:30px;font-weight:500;display:flex;align-items:center;gap:8px;line-height:1}
.fbrand .dot{width:9px;height:9px;border-radius:50%;background:var(--orange)}
.fbrand .tag{font-size:10px;letter-spacing:7px;margin-top:4px;padding-left:28px}
.fabout{left:144px;top:3693px;width:225px;font-size:9.5px;line-height:17px;color:#fff}
.fcol{top:3612px;color:#fff}
.fcol h4{font-size:13px;font-weight:500;margin-bottom:20px}
.fcol li{list-style:none;font-size:10px;margin-bottom:12px}
.fcontact li{display:flex;align-items:center;gap:8px;margin-bottom:14px}
.social{display:flex;gap:18px;margin-top:4px}
.social i{width:14px;height:14px;border-radius:50%;border:1.5px solid #fff}
</style>
</head>
<body>

<!-- Header -->
<div class="abs topbar-accent"></div>
<div class="abs topbar">
  <span><svg width="12" height="12" viewBox="0 0 24 24"><path d="M6.6 10.8a15 15 0 006.6 6.6l2.2-2.2a1 1 0 011-.25 11.4 11.4 0 003.6.6 1 1 0 011 1V20a1 1 0 01-1 1A17 17 0 013 4a1 1 0 011-1h3.5a1 1 0 011 1c0 1.25.2 2.45.6 3.6a1 1 0 01-.25 1z" fill="#F5822A"/></svg>Call now: (202) 555-0148</span>
  <span><svg width="14" height="11" viewBox="0 0 24 18"><rect x="1" y="1" width="22" height="16" rx="2" fill="#F5822A"/><path d="M2 2l10 8 10-8" stroke="#0D1F3F" stroke-width="2" fill="none"/></svg>Email: hello@calderhealth.org</span>
  <span><svg width="12" height="12" viewBox="0 0 24 24"><circle cx="12" cy="12" r="11" fill="#F5822A"/><path d="M12 6v6l4 2" stroke="#fff" stroke-width="2" fill="none"/></svg>Time: Mon - Sun, 08:30am to 05:30pm</span>
</div>
<div class="abs brand"><div class="name">Calder Health <span class="dot"></span></div><div class="tag">SERVICES</div></div>
<nav class="abs nav"><a class="active">Home</a><a>About Us</a><a>Services ⌄</a><a>Blog</a><a>FAQs</a></nav>
<a class="abs btn-contact">Contact Now</a>

<!-- Hero -->
<div class="abs hero-photo" role="img" aria-label="Photo of a nurse and a doctor reviewing notes in a bright clinic hallway"></div>
<section class="abs hero-card">
  <h1>MENTAL WELLNESS<br>FOR A <b>STRONGER YOU</b></h1>
  <p>Evidence-based care tailored to your needs. Where clinical expertise meets your unique needs</p>
  <div class="subscribe"><div class="field">Enter your email</div><div class="go">Subscribe</div></div>
</section>

<!-- Core services -->
<div class="abs sec-title" style="top:700px"><h2>OUR CORE SERVICES</h2></div>

<article class="abs svc" style="left:134px;top:771px">
  <div class="icon"><svg width="46" height="52" viewBox="0 0 46 52" fill="none" stroke="#1B2230" stroke-width="1.6"><path d="M14 44V36c-5-3-8-8-8-14a17 17 0 0134 0l4 8h-4v6a4 4 0 01-4 4h-4v4"/><circle cx="23" cy="21" r="8" stroke="#F5822A"/><path d="M23 13v16M17 19h12" stroke="#F5822A"/><path d="M23 2v3M12 5l2 3M34 5l-2 3M5 12l3 2M41 12l-3 2"/></svg></div>
  <div class="bar"></div>
  <h3>Individual Therapy</h3>
  <p>Lorem Ipsum is simply dummy printing and typesetting industry.</p>
  <a class="more">Read More <svg width="20" height="8" viewBox="0 0 20 8"><path d="M0 4h18M14 1l4 3-4 3" stroke="#F5822A" stroke-width="1.3" fill="none"/></svg></a>
</article>

<article class="abs svc featured" style="left:454px;top:750px">
  <div class="icon"><svg width="60" height="48" viewBox="0 0 60 48" fill="none" stroke="#1B2230" stroke-width="1.8"><circle cx="30" cy="12" r="7"/><path d="M18 40c0-8 5-14 12-14s12 6 12 14z"/><circle cx="12" cy="18" r="5.5"/><path d="M2 40c0-7 4-12 10-12 2 0 4 .5 5 1.5"/><circle cx="48" cy="18" r="5.5"/><path d="M58 40c0-7-4-12-10-12-2 0-4 .5-5 1.5"/></svg></div>
  <div class="bar"></div>
  <h3>Group Sessions</h3>
  <p>Lorem Ipsum is simply dummy printing and typesetting industry.</p>
  <a class="more">Read More <svg width="20" height="8" viewBox="0 0 20 8"><path d="M0 4h18M14 1l4 3-4 3" stroke="#fff" stroke-width="1.3" fill="none"/></svg></a>
</article>

<article class="abs svc" style="left:775px;top:763px">
  <div class="icon"><svg width="36" height="54" viewBox="0 0 36 54" fill="none" stroke="#1B2230" stroke-width="1.6"><rect x="9" y="1" width="18" height="10" rx="2" stroke="#F5822A"/><path d="M13 6h1M18 6h1M23 6h1" stroke="#F5822A"/><circle cx="18" cy="24" r="7"/><path d="M4 50c0-10 6-16 14-16s14 6 14 16z"/><path d="M2 50h32"/></svg></div>
  <div class="bar"></div>
  <h3>Specialized Programs</h3>
  <p>Lorem Ipsum is simply dummy printing and typesetting industry.</p>
  <a class="more">Read More <svg width="20" height="8" viewBox="0 0 20 8"><path d="M0 4h18M14 1l4 3-4 3" stroke="#F5822A" stroke-width="1.3" fill="none"/></svg></a>
</article>

<!-- About -->
<div class="abs rule" style="left:301px;top:1146px"></div>
<div class="abs rule" style="left:789px;top:1146px"></div>
<div class="abs sec-title" style="top:1122px"><h2>ABOUT US</h2><p>Your Path to Peaceful Wellness in the Heart of DC</p></div>
<div class="abs about-panel"></div>
<div class="abs about-figure" role="img" aria-label="Faint outline of a smiling doctor with crossed arms"></div>
<div class="abs about-photo" role="img" aria-label="Photo of a team of doctors and nurses walking down a hospital corridor"></div>
<div class="abs about-text">
  <p>Lorem Ipsum is simply dummy text of the printing and typesetting industry. Lorem Ipsum has been the industry's standard dummy text ever since the 1500s, when an unknown printer took a galley of type and scrambled it to make a type specimen book. It has survived not only five centuries,</p>
  <p>Lorem Ipsum is simply dummy text of the printing and typesetting industry. Lorem Ipsum has been the industry's</p>
  <p>when an unknown printer took a galley of type and scrambled it to make a type specimen book. It has survived not only five centuries, but also the leap into electronic typesetting, remaining essentially unchanged</p>
  <ul>
    <li>There are many variations of passages of Lorem Ipsum available.</li>
    <li>It uses a dictionary of over 200 Latin words,</li>
    <li>Sed ut perspiciatis unde omnis iste natus error sit voluptatem.</li>
  </ul>
  <a class="btn-light" style="margin-top:30px">Read More <svg width="10" height="10" viewBox="0 0 10 10"><path d="M1 9L9 1M3 1h6v6" stroke="#1B2230" stroke-width="1.3" fill="none"/></svg></a>
</div>

<!-- Blog -->
<div class="abs rule" style="left:301px;top:1702px"></div>
<div class="abs rule" style="left:789px;top:1702px"></div>
<div class="abs sec-title" style="top:1680px"><h2>BLOG</h2><p>Your Path to Peaceful Wellness in the Heart of DC</p></div>

<article class="abs post" style="left:141px;top:1739px">
  <div class="img" role="img" aria-label="Photo of a doctor studying brain scans on a monitor" style="background:linear-gradient(90deg,#c8cdd2 0%,#6a7a8c 45%,#0e2a4a 60%,#2b5d8c 100%)"></div>
  <div class="body"><h3>Mind Pain</h3>
  <p>Lorem ipsum dolor sit amet, consectetur adipiscing elit, sed do eiusmod tempor incididunt ut labore et dolore magna aliqua. Ut enim ad minim veniam, quis nostrud exercitation ullamco laboris nisi ut aliquip</p>
  <a class="more">Read More <svg width="20" height="8" viewBox="0 0 20 8"><path d="M0 4h18M14 1l4 3-4 3" stroke="#F5822A" stroke-width="1.3" fill="none"/></svg></a></div>
</article>

<article class="abs post" style="left:618px;top:1739px">
  <div class="img" role="img" aria-label="Photo of a woman shading her eyes in a sunny tropical garden" style="background:linear-gradient(120deg,#3f5a2a 0%,#8aa35a 40%,#c99a7a 60%,#4e6a34 100%)"></div>
  <div class="body"><h3>Mind Fresh Every Day</h3>
  <p>Lorem ipsum dolor sit amet, consectetur adipiscing elit, sed do eiusmod tempor incididunt ut labore et dolore magna aliqua. Ut enim ad minim veniam, quis nostrud exercitation ullamco laboris nisi ut aliquip</p>
  <a class="more">Read More <svg width="20" height="8" viewBox="0 0 20 8"><path d="M0 4h18M14 1l4 3-4 3" stroke="#F5822A" stroke-width="1.3" fill="none"/></svg></a></div>
</article>

<a class="abs btn-dark">View More <svg width="10" height="10" viewBox="0 0 10 10"><path d="M1 9L9 1M3 1h6v6" stroke="#fff" stroke-width="1.3" fill="none"/></svg></a>

<!-- Why choose us -->
<div class="abs rule" style="left:382px;top:2293px"></div>
<div class="abs rule" style="left:709px;top:2293px"></div>
<div class="abs sec-title" style="top:2272px"><h2>WHY CHOOSE US</h2><p>Meet the our team</p></div>
<div class="abs why-panel"></div>
<div class="abs why-text">
  <p>Lorem ipsum dolor sit amet, consectetur adipiscing elit, sed do eiusmod tempor incididunt ut labore et dolore magna aliqua. Ut enim ad minim veniam, quis nostrud exercitation ullamco laboris nisi ut aliquip ex ea commodo consequat. Duis aute irure dolor in reprehenderit in voluptate velit esse cillum dolore eu fugiat nulla pariatur. Excepteur sint occaecat cupidatat non proident, sunt in culpa qui officia deserunt mollit anim id est laborum</p>
  <p>Sed ut perspiciatis unde omnis iste natus error sit voluptatem accusantium doloremque laudantium, totam rem aperiam, eaque ipsa quae ab illo inventore veritatis et quasi architecto beatae vitae dicta sunt explicabo. Nemo enim ipsam voluptatem quia voluptas sit aspernatur aut odit aut fugit, sed quia consequuntur magni dolores eos qui ratione voluptatem sequi nesciunt. Neque porro quisquam est, qui dolorem ipsum quia dolor sit amet, consectetur, adipisci velit, sed quia non numquam eius modi tempora incidunt ut labore et dolore magnam aliquam quaerat voluptatem.</p>
  <a class="btn-light" style="margin-top:22px">Book A call <svg width="10" height="10" viewBox="0 0 10 10"><path d="M1 9L9 1M3 1h6v6" stroke="#1B2230" stroke-width="1.3" fill="none"/></svg></a>
</div>
<div class="abs why-photo" role="img" aria-label="Illustration of a glowing brain hovering above an open hand"></div>

<!-- Testimonials -->
<div class="abs rule" style="left:370px;top:2845px"></div>
<div class="abs rule" style="left:720px;top:2845px"></div>
<div class="abs sec-title" style="top:2823px"><h2>TESTIMONIALS</h2><p>what our clients say about us</p></div>

<svg class="abs" style="left:140px;top:2992px" width="30" height="16" viewBox="0 0 30 16"><circle cx="8" cy="8" r="5" fill="#FCE0C8"/><path d="M28 8H3M9 2L3 8l6 6" stroke="#1B2230" stroke-width="1.6" fill="none"/></svg>
<svg class="abs" style="left:1030px;top:2992px" width="30" height="16" viewBox="0 0 30 16"><circle cx="22" cy="8" r="5" fill="#FCE0C8"/><path d="M2 8h25M21 2l6 6-6 6" stroke="#1B2230" stroke-width="1.6" fill="none"/></svg>

<article class="abs quote" style="left:212px;top:2884px">
  <div class="stars"><svg width="64" height="11" viewBox="0 0 64 11" fill="#F5822A"><path id="st" d="M5.5 0l1.6 3.6 3.9.4-2.9 2.6.8 3.9-3.4-2-3.4 2 .8-3.9L0 4l3.9-.4z"/><use href="#st" x="16"/><use href="#st" x="32"/><use href="#st" x="48"/></svg></div>
  <p>.. followed by some bogus content. Aenean commodo ligula egget dolor. Aenean massa. Cum sociis natoque penatibus et magnis dis parturient montes, nascetur ridiculus mus.</p>
  <div class="person"><div class="avatar" role="img" aria-label="Client portrait"></div><div><b>Maya Brooks</b><span>CEO, Company</span></div></div>
</article>
<article class="abs quote" style="left:478px;top:2884px">
  <div class="stars"><svg width="64" height="11" viewBox="0 0 64 11" fill="#F5822A"><use href="#st"/><use href="#st" x="16"/><use href="#st" x="32"/><use href="#st" x="48"/></svg></div>
  <p>.. followed by some bogus content. Aenean commodo ligula egget dolor. Aenean massa. Cum sociis natoque penatibus et magnis dis parturient montes, nascetur ridiculus mus.</p>
  <div class="person"><div class="avatar" role="img" aria-label="Client portrait"></div><div><b>Maya Brooks</b><span>CEO, Company</span></div></div>
</article>
<article class="abs quote" style="left:745px;top:2884px">
  <div class="stars"><svg width="64" height="11" viewBox="0 0 64 11" fill="#F5822A"><use href="#st"/><use href="#st" x="16"/><use href="#st" x="32"/><use href="#st" x="48"/></svg></div>
  <p>.. followed by some bogus content. Aenean commodo ligula egget dolor. Aenean massa. Cum sociis natoque penatibus et magnis dis parturient montes, nascetur ridiculus mus.</p>
  <div class="person"><div class="avatar" role="img" aria-label="Client portrait"></div><div><b>Maya Brooks</b><span>CEO, Company</span></div></div>
</article>
<div class="abs dots"><i></i><i></i><i></i><i></i><i></i></div>

<!-- Newsletter -->
<div class="abs news-band" role="img" aria-label="Warm orange tinted photo of a clinic waiting room"></div>
<div class="abs news-photo" role="img" aria-label="Photo of a smiling female doctor with a stethoscope holding a tablet"></div>
<h2 class="abs news-title">Subcribe to our Newsletter</h2>
<p class="abs news-copy">Subscribe for Updates: Stay informed about the latest investor updates, financial results, and announcements by subscribing to our newsletter.</p>
<div class="abs subscribe news-form"><div class="field">Enter your email</div><div class="go">Subscribe</div></div>

<!-- Footer -->
<footer class="abs footer"></footer>
<div class="abs fbrand"><div class="name">Calder Health <span class="dot"></span></div><div class="tag">SERVICES</div></div>
<p class="abs fabout">Lorem Ipsum is simply dummy text of the printing and typesetting industry. Lorem Ipsum has been the industry's standard dummy text ever since the 1500s,</p>
<div class="abs fcol" style="left:497px"><h4>Quick &nbsp;link</h4><ul><li>Home</li><li>About Us</li><li>Services</li><li>Blog</li><li>Contact Us</li></ul></div>
<div class="abs fcol" style="left:695px"><h4>Services</h4><ul><li>Individual Therapy</li><li>Group Sessions</li><li>Specialized Programs</li><li>24/7 Available</li></ul></div>
<div class="abs fcol fcontact" style="left:931px"><h4>Contact Details</h4><ul>
  <li><svg width="12" height="12" viewBox="0 0 24 24"><path d="M6.6 10.8a15 15 0 006.6 6.6l2.2-2.2a1 1 0 011-.25 11.4 11.4 0 003.6.6 1 1 0 011 1V20a1 1 0 01-1 1A17 17 0 013 4a1 1 0 011-1h3.5a1 1 0 011 1c0 1.25.2 2.45.6 3.6a1 1 0 01-.25 1z" fill="#F5822A"/></svg>(202) 555-0148</li>
  <li><svg width="14" height="11" viewBox="0 0 24 18"><rect x="1" y="1" width="22" height="16" rx="2" fill="#F5822A"/><path d="M2 2l10 8 10-8" stroke="#0D1F3F" stroke-width="2" fill="none"/></svg>hello@calderhealth.org</li>
</ul>
<div class="social"><i></i><i></i><i></i><i></i></div></div>
<div class="abs footer-bottom">Calder Health © Copyright. All Rights Reserved</div>

</body>
</html>
```